Sparrow Haulage needs a business card design.

Design a double-sided business card for new freight business. On the front, would like to see our logo along with the following info:

Martin Obuya
CEO/FOUNDER
555-206-7142
martinobuya@sparrow-haulage.example

On the reverse side, we would like to use the graphic image of our logo only without the Sparrow Haulage name.

```html
<!DOCTYPE html>
<html lang="en">
<head>
<meta charset="utf-8">
<title>Sparrow Haulage — Business Card</title>
<link rel="stylesheet" href="https://fonts.googleapis.com/css2?family=Roboto:wght@400;500;700&display=swap">
<style>
  :root {
    --backdrop: #9a9a9a;
    --paper: #f7f7f5;
    --navy: #2b2a6b;
    --navy-deep: #1a1856;
    --navy-mid: #2a2a7a;
    --navy-light: #4a4a9c;
    --red: #c8283a;
    --edge-red: #a3161f;
    --ink: #4a4a4a;
    --white: #ffffff;
  }
  * { box-sizing: border-box; margin: 0; padding: 0; }
  html, body {
    width: 1200px; height: 946px; overflow: hidden;
    background: var(--backdrop);
    font-family: "Roboto", Arial, sans-serif;
  }
  .canvas { position: relative; width: 1200px; height: 946px; }

  .card {
    position: absolute;
    width: 620px; height: 354px;
    border-bottom: 4px solid var(--edge-red);
    box-shadow: 0 14px 30px rgba(0,0,0,0.25);
  }

  /* Front */
  .card-front { left: 80px; top: 130px; background: var(--paper); }
  .brand-name {
    position: absolute; right: 52px; top: 72px;
    display: flex; align-items: center; gap: 10px;
    font-weight: 700; font-size: 30px; letter-spacing: 3px;
    color: var(--navy); text-transform: uppercase;
  }
  .brand-mark { width: 18px; height: 18px; background: var(--red); border-radius: 50%; }
  .identity { position: absolute; left: 48px; top: 178px; }
  .person-name { font-weight: 700; font-size: 26px; color: var(--navy); }
  .person-role { font-weight: 400; font-size: 18px; color: var(--red); margin-top: 2px; letter-spacing: 0.3px; }
  .contact-list { list-style: none; margin-top: 12px; }
  .contact-item {
    display: flex; align-items: center; gap: 8px;
    font-size: 17px; color: var(--ink); line-height: 26px;
  }
  .contact-icon { width: 16px; height: 16px; flex: none; }

  /* Back */
  .card-back {
    left: 500px; top: 548px; overflow: hidden;
    background: var(--navy-deep);
  }
  .back-pattern {
    position: absolute; inset: 0;
    background:
      radial-gradient(ellipse at 20% 25%, rgba(150,150,210,0.35) 0%, rgba(150,150,210,0) 55%),
      linear-gradient(135deg, var(--navy-light) 0%, var(--navy-mid) 45%, var(--navy-deep) 100%);
  }
  .back-mark {
    position: absolute; right: 250px; bottom: 92px;
    width: 40px; height: 40px; border-radius: 50%;
    background: var(--white);
  }
</style>
</head>
<body>
<main class="canvas">

  <section class="card card-front" aria-label="Business card front">
    <div class="brand-name"><span class="brand-mark"></span>Sparrow Haulage</div>

    <div class="identity">
      <h1 class="person-name">Martin Obuya</h1>
      <p class="person-role">CEO/FOUNDER</p>
      <ul class="contact-list">
        <li class="contact-item">
          <svg class="contact-icon" viewBox="0 0 24 24" aria-hidden="true"><path fill="var(--navy)" d="M6.6 10.8a15 15 0 0 0 6.6 6.6l2.2-2.2a1 1 0 0 1 1-.25 11.4 11.4 0 0 0 3.6.57 1 1 0 0 1 1 1V20a1 1 0 0 1-1 1A17 17 0 0 1 3 4a1 1 0 0 1 1-1h3.5a1 1 0 0 1 1 1c0 1.25.2 2.45.57 3.57a1 1 0 0 1-.25 1z"/></svg>
          555-206-7142
        </li>
        <li class="contact-item">
          <svg class="contact-icon" viewBox="0 0 24 24" aria-hidden="true"><rect x="2" y="5" width="20" height="14" fill="var(--navy)"/><path d="M2 5l10 8 10-8" fill="none" stroke="var(--paper)" stroke-width="1.6"/></svg>
          martinobuya@sparrow-haulage.example
        </li>
        <li class="contact-item">
          <svg class="contact-icon" viewBox="0 0 24 24" aria-hidden="true"><circle cx="12" cy="12" r="10" fill="var(--navy)"/><path d="M2 12h20M12 2c3 3 3 17 0 20M12 2c-3 3-3 17 0 20" fill="none" stroke="var(--paper)" stroke-width="1.2"/></svg>
          www.sparrow-haulage.example
        </li>
      </ul>
    </div>
  </section>

  <section class="card card-back" aria-label="Business card back">
    <div class="back-pattern" role="img" aria-label="Embossed repeating pattern of the brand symbol across the navy card"></div>
    <span class="back-mark" role="img" aria-label="Brand symbol"></span>
  </section>

</main>
</body>
</html>
```